Detail Shop Business card design

i need a business card design for my new detailing company called 'Brisk's Polish Works'. i want an all black and white design . simple, direct and to the point. i want the designer to choose a fitting font to match the logothe front should have logo, address, phone and email and the back side should have a slogan and text indicating that we offer services on anything including cars, trucks, motorcycles and RVs. slogan will read "we take pride in your ride"
maybe also very small on the back side the IG icon with Brisks_Polish_Works

phone 208.417.6352
address 3847 E Larkin Ave
Spokane WA 99214
email: BrisksPolish@mailvexo.com

Target Market(s)

all ages , auto enthusiasts

Industry/Entity Type

Automotive

Contact Information for Business Card

the front should have logo, address, phone and email and the back side should have a slogan and text indicating that we offer services on anything including cars, trucks, motorcycles and RVs. slogan will read "we take pride in your ride"

phone 208.417.6352
address 3847 E Larkin Ave
Spokane WA 99214

Colors
000000
ffffff

Requirements
Must have
• bold font and very simple design with good spacing
Nice to have
• anything creative from the designer indicating we service any types of vehicles
Should not have
• any colors ,

```html
<!DOCTYPE html>
<html lang="en">
<head>
<meta charset="utf-8">
<title>Brisk's Polish Works – Business Card</title>
<link rel="stylesheet" href="https://fonts.googleapis.com/css2?family=Roboto:wght@400;700&family=Oswald:wght@400&display=swap">
<style>
  :root {
    --ink: #000000;
    --paper: #ffffff;
    --text-grey: #4a4a4a;
    --backdrop: #e6e6e6;
  }
  * { margin: 0; padding: 0; box-sizing: border-box; }
  html, body { width: 1200px; height: 960px; overflow: hidden; }
  body {
    background: var(--backdrop);
    font-family: "Roboto", Arial, sans-serif;
    position: relative;
  }
  .card {
    position: absolute;
    width: 600px;
    height: 343px;
    background: var(--paper);
    box-shadow: 0 2px 6px rgba(0,0,0,0.25);
  }
  .card--front { left: 314px; top: 113px; }
  .card--back  { left: 311px; top: 472px; }

  /* brand name block replacing the mark */
  .brand {
    position: absolute;
    display: flex;
    align-items: center;
    gap: 12px;
    color: var(--ink);
    font-family: "Roboto", Arial, sans-serif;
    font-weight: 700;
    text-transform: uppercase;
    line-height: 1.05;
  }
  .brand__dot {
    flex: none;
    border-radius: 50%;
    background: var(--ink);
  }
  .card--front .brand { right: 24px; top: 70px; font-size: 24px; }
  .card--front .brand__dot { width: 40px; height: 40px; }
  .card--back .brand { left: 0; right: 0; justify-content: center; top: 96px; font-size: 30px; }
  .card--back .brand__dot { width: 48px; height: 48px; }

  /* front: person */
  .person {
    position: absolute;
    left: 24px;
    top: 200px;
  }
  .person::before {
    content: "";
    position: absolute;
    left: -24px;
    top: 0;
    width: 6px;
    height: 36px;
    background: var(--ink);
  }
  .person__name {
    font-weight: 700;
    font-size: 19px;
    color: var(--ink);
    line-height: 22px;
  }
  .person__title {
    font-size: 14px;
    color: var(--text-grey);
    line-height: 18px;
  }

  /* front: contact row */
  .contact {
    position: absolute;
    left: 23px;
    top: 274px;
    display: flex;
    font-size: 14px;
    color: var(--text-grey);
    line-height: 19px;
  }
  .contact__group { padding-right: 14px; }
  .contact__group + .contact__group {
    border-left: 2px solid var(--ink);
    padding-left: 18px;
  }
  .contact__line { display: flex; align-items: center; gap: 8px; white-space: nowrap; }
  .contact__icon { width: 12px; height: 12px; flex: none; fill: var(--ink); }

  /* back: slogan */
  .slogan {
    position: absolute;
    left: 0; right: 0;
    top: 270px;
    text-align: center;
  }
  .slogan__headline {
    display: inline-block;
    font-weight: 700;
    font-size: 17px;
    color: var(--ink);
    padding: 0 38px 2px;
    border-bottom: 1.5px solid var(--ink);
  }
  .slogan__services {
    font-family: "Oswald", "Arial Narrow", sans-serif;
    font-size: 13px;
    color: var(--ink);
    margin-top: 2px;
  }
</style>
</head>
<body>

  <section class="card card--front" aria-label="Card front">
    <div class="brand">
      <span class="brand__dot" aria-hidden="true"></span>
      <span class="brand__name">Brisk's<br>Polish Works</span>
    </div>

    <div class="person">
      <p class="person__name">DALE HARGROVE</p>
      <p class="person__title">CEO/FOUNDER</p>
    </div>

    <div class="contact">
      <div class="contact__group">
        <p class="contact__line">3847 E Larkin Ave</p>
        <p class="contact__line">Spokane WA 99214</p>
      </div>
      <div class="contact__group">
        <p class="contact__line">
          <svg class="contact__icon" viewBox="0 0 12 12" aria-hidden="true"><path d="M2.5 0.5 L4.5 0.5 L5.3 3 L4 4.2 Q5 6.8 7.8 8 L9 6.7 L11.5 7.5 L11.5 9.5 Q11.5 11.5 9.5 11.5 Q0.5 10.5 0.5 2.5 Q0.5 0.5 2.5 0.5 Z"/></svg>
          208.417.6352
        </p>
        <p class="contact__line">
          <svg class="contact__icon" viewBox="0 0 12 12" aria-hidden="true"><path d="M3 0 H9 Q10 0 10 1 V11 Q10 12 9 12 H3 Q2 12 2 11 V1 Q2 0 3 0 Z M3.3 1.5 V9 H8.7 V1.5 Z M6 9.6 A0.9 0.9 0 1 0 6 11.4 A0.9 0.9 0 1 0 6 9.6 Z"/></svg>
          836 521 4073
        </p>
      </div>
      <div class="contact__group">
        <p class="contact__line">
          <svg class="contact__icon" viewBox="0 0 12 12" aria-hidden="true"><path d="M0.5 2.5 H11.5 V10 H0.5 Z M1 3 L6 7 L11 3" stroke="#fff" stroke-width="1"/></svg>
          BrisksPolish@mailvexo.com
        </p>
        <p class="contact__line">
          <svg class="contact__icon" viewBox="0 0 12 12" aria-hidden="true"><circle cx="6" cy="6" r="5.5"/><path d="M0.5 6 H11.5 M6 0.5 Q3 6 6 11.5 M6 0.5 Q9 6 6 11.5" stroke="#fff" stroke-width="0.8" fill="none"/></svg>
          www.briskspolishworks.com
        </p>
      </div>
    </div>
  </section>

  <section class="card card--back" aria-label="Card back">
    <div class="brand">
      <span class="brand__dot" aria-hidden="true"></span>
      <span class="brand__name">Brisk's<br>Polish Works</span>
    </div>

    <div class="slogan">
      <p class="slogan__headline">WE TAKE PRIDE IN YOUR RIDE</p>
      <p class="slogan__services">we offer services on anything including cars, trucks, motorcycles &amp; RVs</p>
    </div>
  </section>

</body>
</html>
```